Dentistry Office

We want a new design for a Dentist's office website.

The theme is: "We provide high quality, state-of-the-art, dental care in a comfortable, caring environment."

The site currently has a menu on the left of the page with about 40 items on it. There is a great deal of textual content on each page, plus several illustrations.

We want to do this using CSS, so we need specifications in the CSS for all possible elements. The CSS needs to be named in a logical manner for easy use.

Every dentist on the planet seems to use lots of Flash. We don't want to because it is so distracting. We are looking for an elegant solution targeting 24-55 age group, but not excluding anyone.

The following (from another dentist's site) can give you a taste of what we want to communicate on the site:

"After 20 years of teaching dentists how to refine their technique and many years of writing textbooks, I currently devote my time to my office and the hands-on practice of dentistry. I'd like to welcome you personally to my dental practice, and I invite you to meet my highly experienced team of professionals.

"We have offered complete dental care of the highest quality since 1978. We provide Preventive Services, Tooth Whitening and Cosmetic Dentistry for a beautiful smile, Endodontics (root canal treatment) to treat painful teeth, Sedation Dentistry so you can relax, and Dental Implants to restore what is missing. We offer total care.

"Our approach to your health is simple: We use our education, experience and dedication to provide every patient with superior dental care.

"This passion for excellence is not just a goal, but a standard every member of our team holds.

"We also pride ourselves with our state of the art procedures, training and technology. This includes creating a beautiful smile using techniques that preserve as much of the original tooth as possible.

"Our abilities are renowned throughout the dental profession and I hope if you have any questions you will contact us by an e-mail note, by phone or just by dropping by."

Keep in mind the screen shape and dimensions. Your design needs to work in the normal screen proportions, regardless of how it looks when you post it here. Scrolling is OK, but the first impression needs to work.
Updates

Keep in mind that there will be about 250 words, or more, on each page.

Competitors web sites:

http://www.brindlecovedentist.example/

http://www.brindlecovedentalcare.example/

http://www.grinsbymarlowvaledental.example/

http://www.tenbyfamilydentalcare.example/

http://www.quelmardental.example/

http://www.dovrinadental.example/

We need to compete with these.

Target Market(s)

Generally adults seeking the most experienced and comfortable-to-be-with dentist.

Industry/Entity Type

Training

Requirements
Must have
• Must stand apart from other dentists.
• Must be elegant.
• Must have a horizontal menu structure across all columns, NOT a vertical that requires scrolling, no popout, pop down, etc. menus.
• We are looking for something special.
• Do not waste your time or ours putting up templates and things you have used before.
• Personally, I do not see how someone outside the US can understand the northern California dental market. But you are welcome to try.
Should not have
• Flash or graphics that move
• The look of a template
• Folksy fonts
• Looks like you used it 20 times before

```html
<!DOCTYPE html>
<html lang="en">
<head>
<meta charset="utf-8">
<title>Daniel Whitcombe, DDS, FAGD – Santa Rosa Dentist</title>
<link href="https://fonts.googleapis.com/css2?family=Tinos:ital,wght@0,400;0,700;1,400&family=Arimo:wght@400;700&display=swap" rel="stylesheet">
<style>
:root{
  --navy:#1e3f6e;
  --navy-dark:#16325a;
  --blue:#2c6aa8;
  --link:#2f6fb6;
  --red:#b2232a;
  --panel:#e6ecf2;
  --panel-line:#c6d2de;
  --text:#333;
  --muted:#666;
  --white:#fff;
}
*{box-sizing:border-box;margin:0;padding:0}
html,body{width:853px;height:1200px;overflow:hidden;background:var(--white)}
body{font-family:"Arimo",Arial,sans-serif;color:var(--text);font-size:8.5px;line-height:1.38}
.page{width:853px;height:1200px;position:relative}

.site-header{height:92px;display:flex;justify-content:space-between;padding:0 0 0 18px;border-top:4px solid var(--navy)}
.brand{padding-top:10px}
.brand-name{font-family:"Tinos",serif;font-size:25px;color:var(--navy);font-weight:400;line-height:1}
.brand-tag{font-family:"Tinos",serif;color:var(--red);font-size:14px;margin-top:4px;padding-left:95px}
.header-contact{width:250px;height:88px;background:linear-gradient(100deg,#f5f7fa 0%,#dfe5ec 45%,#8c9bac 100%);position:relative;padding:8px 0 0 18px;color:var(--navy)}
.header-contact b{font-family:"Tinos",serif;font-size:11px;display:block}
.header-contact span{display:block;font-size:8px}

.main-nav{height:26px;background:var(--navy);display:flex;align-items:center;padding-left:10px}
.main-nav a{color:var(--white);text-decoration:none;font-family:"Tinos",serif;font-size:10.5px;padding:0 10px;border-right:1px solid #5d7aa2}
.main-nav a:last-child{border-right:0}

.hero{height:124px;display:flex;background:var(--navy-dark)}
.hero-copy{width:360px;padding:22px 18px 0 18px;font-family:"Tinos",serif;color:var(--white);font-size:15px;line-height:1.25;background:linear-gradient(90deg,#173766,#2b5585)}
.hero-photo{flex:1;background:linear-gradient(90deg,#2b5585 0%,#8d9eb1 30%,#c9b9a6 60%,#e2d6c8 100%)}

.services{background:var(--panel);border-bottom:1px solid var(--panel-line);display:flex;padding:8px 10px 10px 14px}
.service-col{flex:1;padding-right:6px}
.service-col h3{font-family:"Tinos",serif;color:var(--navy);font-size:11px;margin-bottom:3px}
.service-col ul{list-style:none}
.service-col li{font-size:7.5px;line-height:1.35;padding-left:7px;position:relative;color:#3c4b5c}
.service-col li:before{content:"";position:absolute;left:0;top:4px;width:3px;height:3px;background:var(--blue)}

.content{display:flex;padding:12px 14px 0 18px}
.main-copy{width:545px;padding-right:20px}
.main-copy h1,.main-copy h2{font-family:"Tinos",serif;color:var(--navy);font-weight:700}
.main-copy h1{font-size:17px;margin-bottom:5px}
.main-copy h2{font-size:12px;margin:6px 0 3px}
.main-copy p{margin-bottom:6px}
.main-copy ul{margin:0 0 6px 12px}
.main-copy li{margin-bottom:1px}
.highlight{font-family:"Tinos",serif;color:var(--link);font-size:12.5px;font-weight:700;line-height:1.25;margin:4px 0 6px}
.closing{color:var(--link)}
.signature{font-family:"Tinos",serif;color:var(--link);font-size:15px;margin-top:4px}

.sidebar{flex:1;padding-top:150px}
.sidebar h3{font-family:"Tinos",serif;color:var(--navy);font-size:12px;margin-bottom:3px}
.map-box{border:1px solid var(--panel-line);padding:4px;margin-bottom:100px}
.map-area{height:130px;background:linear-gradient(135deg,#eef1ea,#dde4d8)}
.hours{background:var(--panel);border:1px solid var(--panel-line);padding:8px 10px}
.hours h3{text-align:center}
.hours p{font-size:8px;margin-bottom:4px}
.hours ul{list-style:none}
.hours li{font-size:8px;padding-left:9px;position:relative;margin-bottom:2px;font-weight:700}
.hours li:before{content:"";position:absolute;left:0;top:3px;width:4px;height:4px;background:var(--red)}

.site-footer{position:absolute;left:0;right:0;bottom:0;height:62px;border-top:3px solid var(--navy);background:var(--panel);display:flex;justify-content:space-between;align-items:center;padding:0 18px;font-size:7.5px;color:var(--muted)}
.badges{display:flex;gap:8px}
.badge{width:62px;height:36px;background:var(--white);border:1px solid var(--panel-line)}
</style>
</head>
<body>
<div class="page">
  <header class="site-header">
    <div class="brand">
      <div class="brand-name">Daniel Whitcombe, DDS, FAGD</div>
      <div class="brand-tag">Santa Rosa Dentist</div>
    </div>
    <div class="header-contact" role="img" aria-label="Portrait of the dentist behind the office contact details">
      <b>Daniel Whitcombe, DDS, FAGD</b>
      <span>2870 Larkmead Road, Ste 4</span>
      <span>Santa Rosa, CA 95409</span>
      <span>(707) 555-0142</span>
    </div>
  </header>

  <nav class="main-nav">
    <a href="#">Home</a><a href="#">Why We Are Different?</a><a href="#">Technologies We Offer</a><a href="#">Meet Dr. Whitcombe</a><a href="#">Our Staff</a><a href="#">Contact Us</a><a href="#">Links</a>
  </nav>

  <section class="hero">
    <div class="hero-copy">Santa Rosa Dentist - Daniel Whitcombe, DDS, Providing Cosmetic Dentistry Excellence to Patients in Santa Rosa, Sonoma County and the San Francisco Bay Area.</div>
    <div class="hero-photo" role="img" aria-label="Photograph of smiling patients"></div>
  </section>

  <section class="services">
    <div class="service-col"><h3>Education</h3><ul><li>Emergency Dental Care</li><li>Dental Health</li><li>Your Teeth</li><li>Dental Health Tips</li><li>Making a Smile</li><li>Dentistry Facts</li><li>For Mouth</li><li>Gum Disease</li><li>Patient Forms</li></ul></div>
    <div class="service-col"><h3>Preventative</h3><ul><li>What is Preventive Care</li><li>Taking Care of Your Teeth</li><li>Eating Right</li><li>Dental Check-ups</li><li>Sealants</li><li>Periodontal Disease</li><li>Caring for Gums</li><li>Night Guards</li><li>Mouth Cancer</li><li>Antibiotics with Treatment</li></ul></div>
    <div class="service-col"><h3>Cosmetic</h3><ul><li>Cosmetic Dentistry</li><li>Whitening and Bleaching</li><li>Cosmetic Bonding</li><li>Porcelain Veneers</li><li>Tooth Shaping</li></ul></div>
    <div class="service-col"><h3>Restorations</h3><ul><li>Crowns/Caps: Tooth Repair</li><li>Inlays and Onlays</li><li>Porcelain Bridges</li><li>Bonded Dental Bridges</li><li>Gold Restorations</li><li>Implants</li><li>Treating Cracked Teeth</li><li>Dental Root Treatment</li></ul></div>
    <div class="service-col"><h3>Visiting our office</h3><ul><li>Where to Stay</li><li>Visit with a Map</li><li>Financial Policy</li><li>Dental Insurance</li></ul></div>
  </section>

  <main class="content">
    <article class="main-copy">
      <h1>Welcome To Our Website</h1>
      <p>In Santa Rosa, when you're a patient of Dr. Whitcombe, you can be confident that you're receiving care from the most experienced, knowledgeable, and skilled cosmetic dentist in Sonoma County.</p>
      <p>Dr. Whitcombe is an award-winning leader in restorative dentistry and a great professional. His humor, dedication, and talent ensure you a pleasant experience and superb, long-lasting results.</p>
      <h2>Dr. Whitcombe Provides</h2>
      <ul>
        <li>General dentistry—oral hygiene, cavity detection and repair, crowns</li>
        <li>Cosmetic/aesthetic dentistry—bonded tooth coloured fillings, veneers, whitening and gentle shaping</li>
        <li>Non-metal fillings—natural, durable tooth coloured inlays that are made to last for years</li>
        <li>Tooth shaping—reshaping, lengthening or otherwise improving teeth for improved aesthetics</li>
        <li>Complete smile makeovers to return renewed confidence and a healthy, natural look</li>
        <li>Full and partial dentures breathing options to make teeth appear and feel more real</li>
        <li>Laser Dentistry, Sleep Dentistry, and Implant Dentistry with the Finest and Latest Equipment and Materials</li>
        <li>Dental Implants to replace missing teeth</li>
        <li>Sedation Dentistry so you can be relaxed</li>
      </ul>
      <h2>Dr. Whitcombe' Commitment</h2>
      <p>After 20 years of teaching dentists how to refine their technique and many years of writing textbooks, I currently devote my time to my office and the hands-on practice of dentistry. I'd like to welcome you personally to my dental practice, and I invite you to meet my highly experienced team of professionals.</p>
      <p>We have offered complete dental care of the highest quality since 1978. We provide Preventive Services, Tooth Whitening and Cosmetic Dentistry for a beautiful smile, Endodontics (root canal treatment) to treat painful teeth, Sedation Dentistry so you can relax, and Dental Implants to restore what is missing. We offer total care.</p>
      <p class="highlight">Our approach to your health is simple: We use our education, experience and dedication to provide every patient with superior dental care.</p>
      <p class="highlight">This passion for excellence is not just a goal, but a standard every member of our team holds.</p>
      <p>We also pride ourselves with our state of the art procedures, training and technology. This includes creating a beautiful smile using techniques that preserve as much of the original tooth as possible.</p>
      <p>Our abilities are renowned throughout the dental profession and I hope if you have any questions you will contact us by an e-mail note, by phone or just by dropping by.</p>
      <p class="closing">Thank you,<br>Sincerely,</p>
      <div class="signature">Daniel Whitcombe, DDS FAGD</div>
    </article>

    <aside class="sidebar">
      <div class="map-box">
        <h3>Santa Rosa Map</h3>
        <div class="map-area" role="img" aria-label="Street map showing the office location in Santa Rosa"></div>
      </div>
      <div class="hours">
        <h3>Office Timing</h3>
        <p>Our usual office hours are:</p>
        <ul>
          <li>Monday 8 am to 5 pm</li>
          <li>Tuesday 8 am to 5 pm</li>
          <li>Wednesday 8 am to 5 pm</li>
          <li>Thursday 7 am to 3 pm</li>
          <li>Friday 7.30 am to 3 pm</li>
        </ul>
      </div>
    </aside>
  </main>

  <footer class="site-footer">
    <div>© 2010 DrWhitcombe.example | All rights reserved<br>Office Phone: (707) 555-0142<br>Office Fax: (707) 555-0178</div>
    <div class="badges"><div class="badge"></div><div class="badge"></div><div class="badge"></div></div>
  </footer>
</div>
</body>
</html>
```